Ecommerce web site design for 80s Retro website

we need a website to sell retro gift boxes based around 80's movies, music and gaming
it needs to work with the cartlantic ecommerce provider
there would only be 3 basic gift boxes (music, movies and gaming) , but the packaging would be able to be chosen to match birthdays, Christmas etc.
Each themed box will also have three levels of pricing, classic, premium, ultimate.
the website should be themed around the same colour scheme and look as the logo.

Target Market(s)

People after retro presents and gifts so probably people in their 40s to 50s

Coding

Coded - Design and coding required

Number of Pages Required

1 page

Requirements
Must have
• A real retro look and feel with bright neon colours and some icons or symbols of things from the 80s like tunepods, joysticks, movies, music, gaming etc
Should not have
• A boring bland interface

```html
<!DOCTYPE html>
<html lang="en">
<head>
<meta charset="utf-8">
<title>Neon Attic – Retro Gift Boxes</title>
<link href="https://fonts.googleapis.com/css2?family=Russo+One&family=Roboto:wght@400;500;700&display=swap" rel="stylesheet">
<style>
:root{
  --pink:#e4188f;
  --magenta:#c41dcf;
  --blue:#1ea8ea;
  --indigo:#4f5ff0;
  --ink:#111111;
  --text:#222222;
  --muted:#666666;
  --panel:#eef0f4;
  --white:#ffffff;
  --btn:linear-gradient(90deg,#1ea8ea 0%,#7b4fe8 55%,#e4188f 100%);
}
*{box-sizing:border-box;margin:0;padding:0}
html,body{width:1200px;height:2712px;overflow:hidden}
body{font-family:'Roboto',sans-serif;color:var(--text);background:var(--white);position:relative}
a{color:inherit;text-decoration:none}
.wrap{width:980px;margin:0 auto;position:relative}
.display{font-family:'Russo One',sans-serif}

.topbar{height:35px;background:linear-gradient(90deg,#4f6cf0 0%,#8a3fe0 60%,#c41dcf 100%);color:#fff;font-size:13px}
.topbar .wrap{display:flex;align-items:center;height:35px}
.topbar nav a{margin-right:30px;font-weight:500}
.currency{margin-left:auto;display:flex;align-items:center;gap:8px;font-weight:700;font-size:13px}
.flag{width:16px;height:16px;border-radius:50%;background:linear-gradient(#c33 0 50%,#fff 50% 60%,#c33 60%)}

.header{height:101px}
.header .wrap{display:flex;align-items:center;height:101px}
.brand{font-family:'Roboto',sans-serif;font-weight:700;font-size:22px;color:var(--pink);display:flex;align-items:center;gap:8px;width:295px}
.brand .dot{width:14px;height:14px;background:var(--pink);border-radius:50%}
.search{display:flex;width:424px;height:44px;border:1px solid #ddd;border-radius:22px;overflow:hidden;background:#f3f3f3}
.search .cat{width:158px;display:flex;align-items:center;justify-content:center;font-size:16px;font-weight:500}
.search .field{flex:1;background:#fff;display:flex;align-items:center;padding-left:14px;font-size:12px;color:#888}
.search .go{width:46px;background:var(--pink);display:flex;align-items:center;justify-content:center}
.account{margin-left:36px;font-size:11px;color:#888;line-height:15px}
.account b{display:block;color:var(--ink);font-size:13px;font-weight:500}
.icon-btn{width:42px;height:42px;border-radius:50%;background:#f0f0f0;display:flex;align-items:center;justify-content:center;margin-left:auto}

.mainnav{height:42px;background:var(--ink);color:#fff;font-size:15px;font-weight:500}
.mainnav .wrap{display:flex;align-items:center;height:42px;justify-content:space-between}

.hero{height:510px;background:
  radial-gradient(circle at 50% 26%,#ff2a6d 0 130px,#ff4a90 131px,transparent 175px),
  linear-gradient(180deg,#8a1b8f 0%,#e0307a 30%,#3a3cd8 55%,#2a1f8a 80%,#1a0f55 100%);
  position:relative;color:#fff;text-align:center}
.hero-art{position:absolute;left:490px;top:70px;width:220px;height:145px;border-radius:8px;background:linear-gradient(#c2185b,#6a1b9a);opacity:.55}
.hero h1{position:absolute;top:258px;width:100%;font-family:'Russo One',sans-serif;font-size:40px;letter-spacing:1px}
.hero p{position:absolute;top:318px;left:340px;width:520px;font-size:17px;line-height:27px}
.btn{display:inline-flex;align-items:center;justify-content:center;background:var(--btn);color:#fff;font-weight:700;text-transform:uppercase}
.hero .btn{position:absolute;top:393px;left:520px;width:160px;height:47px;font-size:16px}

.departments{height:552px;background:var(--panel);position:relative}
.section-title{font-family:'Russo One',sans-serif;font-size:31px;text-align:center;color:var(--ink)}
.departments .section-title{padding-top:60px}
.dept-row{position:absolute;top:124px;left:113px;display:flex;gap:20px}
.dept{width:311px;text-align:center}
.dept .frame{height:271px;background:#fff;padding:7px;box-shadow:0 2px 8px rgba(0,0,0,.12)}
.dept .photo{height:100%}
.dept h3{font-size:21px;font-weight:500;margin-top:26px;color:var(--ink)}
.dept .btn{width:110px;height:34px;font-size:14px;margin-top:14px}

.picks{height:855px;position:relative}
.picks .section-title{padding-top:68px}
.grid{position:absolute;top:136px;left:113px;display:grid;grid-template-columns:repeat(4,224px);column-gap:26px;row-gap:28px}
.card{height:299px;background:#fff;box-shadow:0 2px 8px rgba(0,0,0,.13);padding:7px;position:relative}
.card .photo{height:212px;background:#f1f2f4;position:relative}
.tag{position:absolute;top:7px;left:7px;background:linear-gradient(90deg,#7b4fe8,#e4188f);color:#fff;font-size:12px;padding:3px 8px}
.card .meta{display:flex;align-items:center;justify-content:space-between;margin-top:8px}
.quick{font-size:11px;background:#f3f3f3;padding:5px 8px;color:#444}
.card h4{font-size:16px;font-weight:500;margin:8px 0 0 5px;color:var(--ink)}
.price{color:var(--magenta);font-weight:700;font-size:19px;margin:4px 0 0 5px}

.newsletter{height:100px;background:linear-gradient(90deg,#d11ba8 0%,#8e3fd8 45%,#3f7ae8 75%,#1ea8ea 100%);color:#fff}
.newsletter .wrap{display:flex;align-items:center;height:100px}
.newsletter h2{font-family:'Russo One',sans-serif;font-size:31px;line-height:32px}
.newsletter small{display:block;font-size:15px;font-weight:700;margin-top:4px}
.subscribe{margin-left:auto;display:flex;height:42px;width:526px}
.subscribe .field{flex:1;background:#fff;color:#888;font-size:12px;display:flex;align-items:center;padding-left:16px}
.subscribe .go{width:120px;background:var(--ink);display:flex;align-items:center;justify-content:center;font-weight:700;font-size:15px}

.footer{height:517px;text-align:center;position:relative}
.footer .brand{justify-content:center;width:auto;font-size:28px;padding-top:92px}
.footer-links{margin-top:100px;font-size:14px;font-weight:700;color:var(--ink);word-spacing:2px}
.footer-links span{margin:0 24px;font-weight:400}
.copyright{font-size:14px;margin-top:20px;color:#333}
.copyright u{margin:0 4px}
.social{display:flex;justify-content:center;gap:9px;margin-top:24px}
.social a{width:44px;height:44px;border-radius:50%;background:#e3e3e3;display:flex;align-items:center;justify-content:center;font-size:10px;font-weight:700;color:var(--ink)}
.social a:first-child{background:var(--btn);color:#fff}
.payments{display:flex;justify-content:center;gap:4px;margin-top:26px}
.payments span{width:43px;height:28px;border:1px solid #ddd;border-radius:3px;font-size:8px;font-weight:700;display:flex;align-items:center;justify-content:center;color:#333}
</style>
</head>
<body>

<div class="topbar">
  <div class="wrap">
    <nav><a href="#">Home</a><a href="#">About</a><a href="#">Contact</a><a href="#">Your Account</a><a href="#">Register</a><a href="#">Trade Account Registration</a></nav>
    <div class="currency"><span class="flag"></span>USD ($) ▾</div>
  </div>
</div>

<header class="header">
  <div class="wrap">
    <a class="brand" href="#"><span class="dot"></span>Neon Attic</a>
    <div class="search">
      <div class="cat">All Categories ▾</div>
      <div class="field">Search Products...</div>
      <div class="go"><svg width="18" height="18" viewBox="0 0 20 20"><circle cx="8" cy="8" r="6" fill="none" stroke="#fff" stroke-width="2.5"/><line x1="12.5" y1="12.5" x2="17" y2="17" stroke="#fff" stroke-width="2.5"/></svg></div>
    </div>
    <div class="account">Hello Sign in<b>Accounts &amp; Lists ⌄</b></div>
    <svg style="margin-left:12px" width="30" height="32" viewBox="0 0 30 32"><circle cx="15" cy="10" r="7" fill="none" stroke="#222" stroke-width="2"/><path d="M3 30c0-8 6-12 12-12s12 4 12 12z" fill="none" stroke="#222" stroke-width="2"/></svg>
    <div class="icon-btn"><svg width="20" height="18" viewBox="0 0 24 22"><path d="M12 20 3 11a5 5 0 0 1 9-6 5 5 0 0 1 9 6z" fill="none" stroke="#222" stroke-width="2"/></svg></div>
  </div>
</header>

<nav class="mainnav">
  <div class="wrap">
    <a href="#">Movies Box</a><a href="#">Music Box</a><a href="#">Gaming Box</a><a href="#">Inspiration</a><a href="#">New</a><a href="#">Sale</a><a href="#">Brands</a><a href="#">Gift Voucher</a><a href="#">Blog</a><a href="#">Basket (0 Items) 🛒</a>
  </div>
</nav>

<section class="hero">
  <div class="hero-art" role="img" aria-label="Neon synthwave sun over a glowing wireframe mountain landscape"></div>
  <h1>RETRO GIFT BOXES</h1>
  <p>Lorem ipsum dolor sit amet, consectetur adipiscing elit, sed do incididunt ut labore et dolore magna aliqua.</p>
  <a class="btn" href="#">Shop Now</a>
</section>

<section class="departments">
  <h2 class="section-title">MOST POPULAR DEPARTMENTS</h2>
  <div class="dept-row">
    <div class="dept">
      <div class="frame"><div class="photo" role="img" aria-label="Vintage film reels and canisters" style="background:linear-gradient(135deg,#d9d9d9,#3a3a3a 60%,#c9a23a)"></div></div>
      <h3>Movies</h3><a class="btn" href="#">Shop Now</a>
    </div>
    <div class="dept">
      <div class="frame"><div class="photo" role="img" aria-label="Stack of colourful board game boxes" style="background:linear-gradient(180deg,#2b4fb5,#1d2f8a 50%,#3aa04a)"></div></div>
      <h3>Games</h3><a class="btn" href="#">Shop Now</a>
    </div>
    <div class="dept">
      <div class="frame"><div class="photo" role="img" aria-label="Antique music box mechanism on sheet music" style="background:radial-gradient(circle at 50% 55%,#8a6a30,#3d2a12 70%)"></div></div>
      <h3>Music</h3><a class="btn" href="#">Shop Now</a>
    </div>
  </div>
</section>

<section class="picks">
  <h2 class="section-title">OUR TOP PICKS THIS YEAR</h2>
  <div class="grid">
    <article class="card"><div class="photo" role="img" aria-label="Ornate wooden music box" style="background:radial-gradient(circle,#8a3a22 0 35%,#f1f2f4 60%)"></div><div class="meta"><span class="quick">Quick View</span><svg width="20" height="18" viewBox="0 0 24 22"><path d="M12 20 3 11a5 5 0 0 1 9-6 5 5 0 0 1 9 6z" fill="none" stroke="#333" stroke-width="2"/></svg></div><h4>Lorem ipsum dolor sit amet</h4><div class="price">$39.95</div></article>
    <article class="card"><div class="photo" role="img" aria-label="Cardboard box of film reels" style="background:radial-gradient(circle,#b89a6a 0 30%,#f1f2f4 60%)"><span class="tag">Classic</span></div><div class="meta"><span class="quick">Quick View</span><svg width="20" height="18" viewBox="0 0 24 22"><path d="M12 20 3 11a5 5 0 0 1 9-6 5 5 0 0 1 9 6z" fill="none" stroke="#333" stroke-width="2"/></svg></div><h4>Lorem ipsum dolor sit amet</h4><div class="price">$39.95</div></article>
    <article class="card"><div class="photo" role="img" aria-label="Treasure chest of gaming dice" style="background:radial-gradient(circle,#c98a3a 0 28%,#f1f2f4 60%)"></div><div class="meta"><span class="quick">Quick View</span><svg width="20" height="18" viewBox="0 0 24 22"><path d="M12 20 3 11a5 5 0 0 1 9-6 5 5 0 0 1 9 6z" fill="none" stroke="#333" stroke-width="2"/></svg></div><h4>Lorem ipsum dolor sit amet</h4><div class="price">$39.95</div></article>
    <article class="card"><div class="photo" role="img" aria-label="Red film-themed gift box" style="background:radial-gradient(circle,#d22a2a 0 32%,#f1f2f4 60%)"><span class="tag">Premium</span></div><div class="meta"><span class="quick">Quick View</span><svg width="20" height="18" viewBox="0 0 24 22"><path d="M12 20 3 11a5 5 0 0 1 9-6 5 5 0 0 1 9 6z" fill="none" stroke="#333" stroke-width="2"/></svg></div><h4>Lorem ipsum dolor sit amet</h4><div class="price">$39.95</div></article>
    <article class="card"><div class="photo" role="img" aria-label="Box of sports equipment" style="background:radial-gradient(circle,#c88a5a 0 30%,#f1f2f4 60%)"><span class="tag">Ultimate</span></div><div class="meta"><span class="quick">Quick View</span><svg width="20" height="18" viewBox="0 0 24 22"><path d="M12 20 3 11a5 5 0 0 1 9-6 5 5 0 0 1 9 6z" fill="none" stroke="#333" stroke-width="2"/></svg></div><h4>Lorem ipsum dolor sit amet</h4><div class="price">$39.95</div></article>
    <article class="card"><div class="photo" role="img" aria-label="Open wooden music box" style="background:radial-gradient(circle,#9a5a2a 0 30%,#f1f2f4 60%)"></div><div class="meta"><span class="quick">Quick View</span><svg width="20" height="18" viewBox="0 0 24 22"><path d="M12 20 3 11a5 5 0 0 1 9-6 5 5 0 0 1 9 6z" fill="none" stroke="#333" stroke-width="2"/></svg></div><h4>Lorem ipsum dolor sit amet</h4><div class="price">$39.95</div></article>
    <article class="card"><div class="photo" role="img" aria-label="Video cassettes in a cardboard box" style="background:radial-gradient(circle,#2a2a2a 0 22%,#d8c8b0 38%,#f1f2f4 62%)"><span class="tag">Classic</span></div><div class="meta"><span class="quick">Quick View</span><svg width="20" height="18" viewBox="0 0 24 22"><path d="M12 20 3 11a5 5 0 0 1 9-6 5 5 0 0 1 9 6z" fill="none" stroke="#333" stroke-width="2"/></svg></div><h4>Lorem ipsum dolor sit amet</h4><div class="price">$39.95</div></article>
    <article class="card"><div class="photo" role="img" aria-label="Carved wooden hand-crank music box" style="background:radial-gradient(circle,#b88a3a 0 28%,#f1f2f4 58%)"></div><div class="meta"><span class="quick">Quick View</span><svg width="20" height="18" viewBox="0 0 24 22"><path d="M12 20 3 11a5 5 0 0 1 9-6 5 5 0 0 1 9 6z" fill="none" stroke="#333" stroke-width="2"/></svg></div><h4>Lorem ipsum dolor sit amet</h4><div class="price">$39.95</div></article>
  </div>
</section>

<section class="newsletter">
  <div class="wrap">
    <div><h2>WHAT'S NEW WITH US?</h2><small>Sign Up To Our Newsletter For Our Latest Updates</small></div>
    <div class="subscribe"><div class="field">Enter your email address</div><div class="go">SUBSCRIBE</div></div>
  </div>
</section>

<footer class="footer">
  <a class="brand" href="#"><span class="dot"></span>Neon Attic</a>
  <div class="footer-links">HOME<span>|</span>ABOUT US<span>|</span>FAQs<span>|</span>CONTACT US<span>|</span>DELIVERY<span>|</span>TERMS<span>|</span>PRIVACY<span>|</span>RETURNS</div>
  <p class="copyright">Copyright© 2022 <u>Neon Attic</u> | All Rights Reserved</p>
  <div class="social"><a href="#">Pixo</a><a href="#">Chirp</a><a href="#">Linkd</a><a href="#">Snapo</a></div>
  <div class="payments"><span>PayVault</span><span>MintCard</span><span>Veyra</span><span>Scoutpay</span><span>Amberex</span><span>Jadeca</span><span>Moresto</span></div>
</footer>

</body>
</html>
```